Travel Agency Website - Simple General

Need a 7 page simple design that is pretty repetitive. Need to be able to load quickly that is SEO optimized. Trying to give ideas on what they can do, be personal as we are local, but at the same time come across as professional and get information easily with little burden.

- Landing Page
- Brimwell Vacations Page
- Family Trips
- Road Trips from Texas
- Other Destinations
- About Us Page
- Contact Us Page

Target Market(s)

Families

Coding

Coded - Design and coding required

Number of Pages Required

5+ page

Colors

Designer to choose colors to be used in the design.

Requirements
Must have
• Like it to flow easily with our logo. Use that for colors, etc.

```html
<!DOCTYPE html>
<html lang="en">
<head>
<meta charset="utf-8">
<title>Wander Lane Travel — Family Adventures from Texas</title>
<meta name="description" content="Locally owned family travel planning: Brimwell vacations, family trips, Texas road trips and more.">
<link href="https://fonts.googleapis.com/css2?family=Poppins:wght@400;500;600&family=Great+Vibes&display=swap" rel="stylesheet">
<style>
:root{
  --teal:#1c5962;
  --teal-dark:#123f46;
  --gold:#c3994f;
  --gold-light:#d8b37a;
  --cream:#fdf8f1;
  --cream-2:#fcefdf;
  --ink:#222;
  --muted:#555;
  --footer:#0e2a2f;
  --white:#fff;
  --line:#e3ddd3;
}
*{box-sizing:border-box;margin:0;padding:0}
html,body{width:1200px;height:4699px;overflow:hidden}
body{font-family:'Poppins',sans-serif;color:var(--ink);background:var(--cream);position:relative}
.abs{position:absolute}
.script{font-family:'Great Vibes',cursive;color:var(--gold);font-weight:400}
.title{color:var(--teal);font-weight:600;letter-spacing:-.5px}
.rule{width:60px;height:4px;background:var(--gold);border-radius:2px}
.btn{display:inline-flex;align-items:center;gap:12px;background:var(--gold);color:#fff;font-size:13px;font-weight:600;border-radius:30px;padding:6px 6px 6px 18px;text-transform:uppercase;white-space:nowrap}
.btn .arrow{width:32px;height:32px;border-radius:50%;border:2px solid #fff;display:flex;align-items:center;justify-content:center}
.img{position:absolute}

/* hero */
.hero{top:0;left:0;width:1200px;height:563px;background:radial-gradient(ellipse at 50% 55%,#3fb8c4 0%,#1f8c99 28%,#2e6e6a 50%,#8a4a2c 75%,#5a3a26 100%)}
.nav{top:14px;left:0;width:1200px;height:60px}
.brand{left:140px;top:0;width:120px;height:60px;display:flex;align-items:center;gap:8px;color:#fff;font-weight:600;font-size:15px;line-height:1.1}
.brand .dot{width:14px;height:14px;border-radius:50%;background:#fff;flex:none}
.menu{left:404px;top:22px;display:flex;gap:20px;font-size:12px;color:#fff}
.nav-cta{position:absolute;left:905px;top:10px;font-size:12px}
.hero-text{top:185px;left:0;width:1200px;text-align:center;color:#fff}
.hero-text .script{color:#fff;font-size:52px;line-height:1}
.hero-text h1{font-size:66px;font-weight:600;line-height:1.02;letter-spacing:-1px}
.hero-cta{position:absolute;left:438px;top:396px}

/* journey */
.journey-head{top:662px;left:0;width:1200px;text-align:center}
.journey-head .script{font-size:38px;line-height:1}
.journey-head h2{font-size:34px;margin-top:-4px}
.journey-head .rule{margin:8px auto 22px}
.journey-head p{font-size:13px}
.card{width:444px;height:388px;border-radius:16px;overflow:hidden}
.card .photo{position:absolute;inset:0;border-radius:16px}
.card .label{position:absolute;left:14px;right:14px;bottom:0;height:110px;background:#fff;border-radius:12px;box-shadow:0 6px 18px rgba(0,0,0,.08);padding:18px}
.tag{display:inline-block;font-size:10px;color:#fff;border-radius:10px;padding:3px 10px;margin-bottom:6px}
.label h3{font-size:22px;font-weight:500;color:#1a1a1a}
.label small{font-size:11px;text-transform:uppercase}
.go{position:absolute;right:18px;top:40px;width:32px;height:32px;border-radius:50%;background:var(--teal);display:flex;align-items:center;justify-content:center}

/* texas */
.texas{top:1685px;left:0;width:1200px;height:375px;background:linear-gradient(90deg,#6d7a3e 0%,#8d8a4e 35%,#b8cbd3 60%,#c9d9de 100%)}
.texas-box{left:644px;top:51px;width:410px;height:270px;background:#fff;border-radius:12px;padding:24px 20px 24px 24px}
.texas-box .script{font-size:30px;line-height:1}
.texas-box h2{font-size:31px;line-height:1.2;margin-top:8px;white-space:nowrap}
.texas-box p{font-size:12px;margin:8px 0 18px;line-height:1.5}

/* about */
.about-text{left:140px;top:2155px;width:380px}
.about-text .script{font-size:34px;line-height:1}
.about-text h2{font-size:34px;line-height:1.15;margin-top:2px}
.about-text .rule{margin:10px 0 18px}
.about-text p{font-size:12.3px;line-height:1.8;margin-bottom:4px}
.about-text .btn{margin-top:26px}

/* why */
.why{top:2680px;left:0;width:1200px;height:677px;background:var(--cream-2)}
.why-head{top:82px;left:0;width:1200px;text-align:center}
.why-head .script{font-size:38px;line-height:1}
.why-head h2{font-size:34px;margin-top:-4px}
.why-head .rule{margin:8px auto 22px}
.why-head p{font-size:13px}
.feat{width:230px;font-size:12.5px;line-height:1.5}
.feat b{display:block;font-size:14.5px;font-weight:600}
.feat.right{text-align:right}
.ico{width:62px;height:62px;border-radius:50%;background:#fff;box-shadow:0 4px 12px rgba(0,0,0,.08);display:flex;align-items:center;justify-content:center}

/* contact */
.contact-head{top:3430px;left:0;width:1200px;text-align:center}
.contact-head .script{font-size:36px;line-height:1}
.contact-head h2{font-size:34px;margin-top:-2px}
.field{background:#fff;border:1px solid var(--line);border-radius:4px;font-size:12px;color:#888;display:flex;align-items:flex-start;gap:10px;padding:18px 16px}
.field .sep{width:1px;height:14px;background:#ccc}
.submit{left:292px;top:3810px;width:616px;height:53px;background:var(--gold);color:#fff;font-size:12.5px;font-weight:600;display:flex;align-items:center;justify-content:center;border-radius:3px}

/* subscribe */
.subscribe{top:3930px;left:0;width:1200px;height:380px;background:linear-gradient(180deg,var(--cream) 0%,var(--cream) 32%,#cfd3cf 55%,#8a968d 78%,#5f6d63 100%)}
.sub-head{top:40px;left:0;width:1200px;text-align:center}
.sub-head .script{font-size:34px;line-height:1}
.sub-head h2{font-size:34px;line-height:1;margin-top:-2px}
.sub-head p{font-size:12.5px;margin-top:22px}
.sub-bar{left:282px;top:195px;width:632px;height:60px;background:#fff;border-radius:30px;box-shadow:0 4px 14px rgba(0,0,0,.1);display:flex;align-items:center;padding:0 6px 0 28px;color:#777;font-size:15px}
.sub-bar .btn-sub{margin-left:auto;background:var(--teal);color:#fff;font-size:13px;font-weight:600;border-radius:26px;height:48px;padding:0 24px;display:flex;align-items:center;gap:10px}

/* footer */
.footer{top:4310px;left:0;width:1200px;height:389px;background:var(--footer);color:#fff}
.fcol h4{font-size:17px;font-weight:500;letter-spacing:.3px;margin-bottom:12px}
.fcol li{list-style:none;font-size:13px;line-height:27px}
.crow{display:flex;gap:10px;font-size:12.5px;line-height:20px;margin-bottom:10px}
.soc{display:flex;align-items:center;gap:12px;font-size:13px;margin-bottom:15px}
.soc .c{width:28px;height:28px;border-radius:50%;border:1px solid #fff}
.soc .c.f{background:var(--gold);border-color:var(--gold)}
.fbrand{left:828px;top:80px;width:230px;height:200px;display:flex;align-items:center;justify-content:center;gap:10px;font-size:22px;font-weight:600}
.fbrand .dot{width:18px;height:18px;border-radius:50%;background:var(--gold);flex:none}
.copy{top:360px;left:0;width:1200px;text-align:center;font-size:12px}
</style>
</head>
<body>

<header class="abs hero">
  <div class="img" role="img" aria-label="Turquoise cove between red cliffs with a kayak on the water" style="inset:0"></div>
  <nav class="abs nav">
    <div class="abs brand"><span class="dot"></span>Wander Lane<br>Travel</div>
    <div class="abs menu"><span>HOME</span><span>BRIMWELL</span><span>FAMILY TRIPS</span><span>ROAD TRIPS</span><span>DESTINATIONS</span><span>ABOUT US</span></div>
    <a class="btn nav-cta">Contact Us<span class="arrow"><svg width="14" height="14" viewBox="0 0 14 14"><path d="M1 7h11M8 3l4 4-4 4" stroke="#fff" stroke-width="1.8" fill="none"/></svg></span></a>
  </nav>
  <div class="abs hero-text">
    <div class="script">Adventure Start</div>
    <h1>Your Family<br>Adventure Awaits</h1>
  </div>
  <a class="btn hero-cta">Start Planning Now<span class="arrow"><svg width="14" height="14" viewBox="0 0 14 14"><path d="M1 7h11M8 3l4 4-4 4" stroke="#fff" stroke-width="1.8" fill="none"/></svg></span></a>
</header>

<section>
  <div class="abs journey-head">
    <div class="script">Whist</div>
    <h2 class="title">Begin Your Journey.</h2>
    <div class="rule"></div>
    <p>Curated adventures for every family rhythm</p>
  </div>

  <article class="abs card" style="left:140px;top:800px">
    <div class="photo" role="img" aria-label="Family relaxing on the deck of a sailboat" style="background:linear-gradient(160deg,#dfe6ea,#9fb3bd 50%,#c7a789)"></div>
    <div class="label"><span class="tag" style="background:var(--gold)">Signature</span><h3>Brimwell Vacations</h3><small>Land and Sea</small>
      <span class="go"><svg width="14" height="14" viewBox="0 0 14 14"><path d="M1 7h11M8 3l4 4-4 4" stroke="#fff" stroke-width="1.8" fill="none"/></svg></span></div>
  </article>
  <article class="abs card" style="left:615px;top:800px">
    <div class="photo" role="img" aria-label="Family standing on a green clifftop above the sea" style="background:linear-gradient(160deg,#b8d2e0,#7e9a63 55%,#556a3b)"></div>
    <div class="label"><span class="tag" style="background:#2f9a57">For All Ages</span><h3>Family Trips</h3><small>Bonding &amp; Adventure</small>
      <span class="go"><svg width="14" height="14" viewBox="0 0 14 14"><path d="M1 7h11M8 3l4 4-4 4" stroke="#fff" stroke-width="1.8" fill="none"/></svg></span></div>
  </article>
  <article class="abs card" style="left:140px;top:1209px">
    <div class="photo" role="img" aria-label="Traveler walking down a desert road toward red buttes" style="background:linear-gradient(180deg,#cfe0ea,#e7c8a6 40%,#c06a3c 65%,#8a5a44)"></div>
    <div class="label"><span class="tag" style="background:#1f6fd1">Partnered</span><h3>Texas Road Trips</h3><small>Pine Ridge Van Rentals</small>
      <span class="go"><svg width="14" height="14" viewBox="0 0 14 14"><path d="M1 7h11M8 3l4 4-4 4" stroke="#fff" stroke-width="1.8" fill="none"/></svg></span></div>
  </article>
  <article class="abs card" style="left:615px;top:1209px">
    <div class="photo" role="img" aria-label="Family walking along a sunny beach" style="background:linear-gradient(180deg,#a9cbe6,#4a8fb7 45%,#e8dcc6 75%)"></div>
    <div class="label"><span class="tag" style="background:#2f9a57">Beyond</span><h3>Other Destinations</h3><small>Beaches, Mountains &amp; Cities</small>
      <span class="go"><svg width="14" height="14" viewBox="0 0 14 14"><path d="M1 7h11M8 3l4 4-4 4" stroke="#fff" stroke-width="1.8" fill="none"/></svg></span></div>
  </article>
</section>

<section class="abs texas">
  <div class="img" role="img" aria-label="Smiling family on a coastal hilltop" style="inset:0"></div>
  <div class="abs texas-box">
    <div class="script">Begin Your Adventure</div>
    <h2 class="title">Best Texas<br>Getaways for Families</h2>
    <p>From Gulf Coast Science Center to San Antonio river walks create memories that last a lifetime.</p>
    <a class="btn">See Family Packages<span class="arrow"><svg width="14" height="14" viewBox="0 0 14 14"><path d="M1 7h11M8 3l4 4-4 4" stroke="#fff" stroke-width="1.8" fill="none"/></svg></span></a>
  </div>
</section>

<section>
  <div class="abs about-text">
    <div class="script">About</div>
    <h2 class="title">Wander Lane<br>Travel</h2>
    <div class="rule"></div>
    <p>We assist families with planning trips, organizing itineraries, and selecting destinations that fit their needs. From Brimwell vacations to Texas road adventures, let’s craft memories that last a lifetime.</p>
    <p>We don’t just book trips — we craft story-filled journeys. With deep local partnerships and expert knowledge of family-friendly destinations, every detail is designed to reduce stress and increase wonder. From Brimwell magic to Texas open roads, your next chapter starts here.</p>
    <a class="btn">Read More<span class="arrow"><svg width="14" height="14" viewBox="0 0 14 14"><path d="M1 7h11M8 3l4 4-4 4" stroke="#fff" stroke-width="1.8" fill="none"/></svg></span></a>
  </div>
  <div class="img" role="img" aria-label="Family with bicycles reading a map by the sea" style="left:565px;top:2160px;width:241px;height:197px;border-radius:12px;background:linear-gradient(180deg,#e9dccb,#b9c3c6 60%,#8c8a80)"></div>
  <div class="img" role="img" aria-label="Friends swimming beside a boat in clear water" style="left:565px;top:2367px;width:241px;height:221px;border-radius:12px;background:linear-gradient(180deg,#cbd3d3,#5fa7a3 55%,#3f8e7e)"></div>
  <div class="img" role="img" aria-label="Friends relaxing on a boat deck near limestone cliffs" style="left:818px;top:2206px;width:241px;height:336px;border-radius:12px;background:linear-gradient(180deg,#6a8a7a,#2f8fb0 45%,#c9c4bb 75%)"></div>
</section>

<section class="abs why">
  <div class="abs why-head">
    <div class="script">Whist</div>
    <h2 class="title">Why Choose Us</h2>
    <div class="rule"></div>
    <p>Locally owned, personally crafted — we turn vacations into stories.</p>
  </div>
  <svg class="abs" style="left:400px;top:245px" width="400" height="400" viewBox="0 0 400 400"><circle cx="200" cy="200" r="188" fill="none" stroke="#cfc3ae" stroke-dasharray="3 5"/></svg>
  <div class="abs" role="img" aria-label="Beach chairs by the sea behind the agency name" style="left:454px;top:253px;width:292px;height:290px;border-radius:50%;background:radial-gradient(circle,#eaf1f0 0%,#a9c7c6 50%,#6e8f86 100%)"></div>
  <div class="abs" style="left:454px;top:380px;width:292px;text-align:center;color:var(--teal);font-size:26px;font-weight:600">Wander Lane</div>

  <div class="abs feat right" style="left:167px;top:243px"><b>Local Expertise</b>Texas-based family, we know the best road trips &amp; hidden gems.</div>
  <div class="abs ico" style="left:413px;top:240px"><svg width="30" height="30" viewBox="0 0 30 30"><path d="M4 8l7-3 8 3 7-3v17l-7 3-8-3-7 3z" fill="none" stroke="var(--teal)" stroke-width="2"/><circle cx="15" cy="12" r="3" fill="var(--gold)"/></svg></div>

  <div class="abs ico" style="left:725px;top:240px"><svg width="30" height="30" viewBox="0 0 30 30"><path d="M4 18h22l-3 6H7z" fill="var(--teal)"/><rect x="9" y="11" width="12" height="6" fill="var(--gold)"/></svg></div>
  <div class="abs feat" style="left:817px;top:245px"><b>Ark &amp; Cruise Expert</b>Brimwell World,<br>Land, Cruise Lines.</div>

  <div class="abs feat right" style="left:114px;top:400px"><b>Personalized Planning</b>Tailored to your family’s style, budget and dreams.</div>
  <div class="abs ico" style="left:360px;top:398px"><svg width="30" height="30" viewBox="0 0 30 30"><rect x="7" y="5" width="16" height="21" rx="2" fill="var(--teal)"/><path d="M11 12h8M11 16h8M11 20h5" stroke="#fff" stroke-width="1.6"/></svg></div>

  <div class="abs ico" style="left:775px;top:398px"><svg width="30" height="30" viewBox="0 0 30 30"><path d="M6 6h8v8h8v10l-6-4-4 4v-6H6z" fill="var(--teal)"/></svg></div>
  <div class="abs feat" style="left:858px;top:392px"><b>Texas Road Trips</b>Texas-based family, we know the best road trips &amp; hidden gems.</div>

  <div class="abs feat right" style="left:178px;top:528px"><b>Trusted Partners</b>Brimwell, Pine Ridge Van Rentals, cruise lines &amp; more.</div>
  <div class="abs ico" style="left:424px;top:530px"><svg width="30" height="30" viewBox="0 0 30 30"><path d="M4 16l6-5 5 3 5-3 6 5-8 7z" fill="var(--teal)"/><circle cx="15" cy="8" r="3" fill="var(--gold)"/></svg></div>

  <div class="abs ico" style="left:710px;top:540px"><svg width="30" height="30" viewBox="0 0 30 30"><circle cx="10" cy="10" r="4" fill="var(--teal)"/><circle cx="20" cy="10" r="4" fill="var(--teal)"/><path d="M3 24a7 7 0 0 1 14 0zM13 24a7 7 0 0 1 14 0z" fill="var(--teal)"/></svg></div>
  <div class="abs feat" style="left:791px;top:535px"><b>100% Family Focus</b>We only serve families — that’s<br>our heartbeat.</div>
</section>

<section>
  <div class="abs contact-head">
    <div class="script">General Inquiry</div>
    <h2 class="title">Ready To Wander? Let's Talk</h2>
  </div>
  <form>
    <label class="abs field" style="left:292px;top:3545px;width:302px;height:53px"><span>👤</span><span class="sep"></span>First Name</label>
    <label class="abs field" style="left:606px;top:3545px;width:302px;height:53px"><span>👤</span><span class="sep"></span>Last Name</label>
    <label class="abs field" style="left:292px;top:3613px;width:302px;height:53px"><span>✉</span><span class="sep"></span>Your Email</label>
    <label class="abs field" style="left:606px;top:3613px;width:302px;height:53px"><span>☎</span><span class="sep"></span>Phone</label>
    <label class="abs field" style="left:292px;top:3681px;width:616px;height:107px"><span>✎</span><span class="sep"></span>Your Message</label>
    <div class="abs submit">SUBMIT NOW</div>
  </form>
</section>

<section class="abs subscribe">
  <div class="img" role="img" aria-label="Misty green mountains under low clouds" style="inset:0"></div>
  <div class="abs sub-head">
    <div class="script">Subscribe Now</div>
    <h2 class="title">Subscribe For Latest Update<br>About Travelling</h2>
    <p>Latest Updates, Exclusive Content, And Special Offers? Subscribe To Our Newsletter!</p>
  </div>
  <div class="abs sub-bar">✉&nbsp; Your Email<span class="btn-sub">SUBSCRIBE <svg width="16" height="12" viewBox="0 0 16 12"><path d="M1 6h13M10 2l4 4-4 4" stroke="#fff" stroke-width="1.6" fill="none"/></svg></span></div>
</section>

<footer class="abs footer">
  <div class="abs fcol" style="left:140px;top:68px">
    <h4>QUICK LINKS</h4>
    <ul><li>Home</li><li>Brimwell</li><li>Family Trips</li><li>Road Trips</li><li>Destinations</li><li>About Us</li><li>Contact Us</li></ul>
  </div>
  <div class="abs fcol" style="left:330px;top:68px">
    <h4>CONTACT DETAILS</h4>
    <div class="crow"><svg width="14" height="16" viewBox="0 0 14 16"><path d="M7 15s5-5 5-9A5 5 0 0 0 2 6c0 4 5 9 5 9z" fill="#fff"/><circle cx="7" cy="6" r="2" fill="var(--footer)"/></svg><span>410 Cedar Hollow Rd.<br>Tyler, TX 75701</span></div>
    <div class="crow"><svg width="14" height="14" viewBox="0 0 14 14"><path d="M3 1l3 3-2 2a8 8 0 0 0 4 4l2-2 3 3-2 2C6 13 1 8 1 3z" fill="#fff"/></svg><span>Phone<br>555.010.2244</span></div>
    <div class="crow"><svg width="14" height="12" viewBox="0 0 14 12"><rect x="1" y="1" width="12" height="10" fill="#fff"/><path d="M1 1l6 5 6-5" stroke="var(--footer)" fill="none"/></svg><span>Email<br>hello@wanderlanetravel.com</span></div>
  </div>
  <div class="abs fcol" style="left:617px;top:68px">
    <h4>SOCIAL MEDIA</h4>
    <div class="soc"><span class="c f"></span>Facepage</div>
    <div class="soc"><span class="c"></span>ViewTube</div>
    <div class="soc"><span class="c"></span>LinkPro</div>
    <div class="soc"><span class="c"></span>Snapgram</div>
  </div>
  <div class="abs fbrand"><span class="dot"></span>Wander Lane Travel</div>
  <div class="abs copy">© 2026 Wander Lane Travel. All Rights Reserved.</div>
</footer>

</body>
</html>
```